Business card for a Exhibition booth fabrication company

Hi. My company would like to change our corporate name card. We are an events and Exhibition stand builder company. We would like our corporate name card to resonate what we do. I need someone to create something unique that relates to the industry that I am in. The graphic designer should be creative to incorporate the elements of my industry and try to blend in well in the design of the card. Our aim is to ensure that we are unique and our card can look different from our competitors.
Updates

Target Market(s)

Marketing and events manager from all companies

Contact Information for Business Card

The business card should have the following details:
Name
Job Title
Email
Website

Colors

Designer to choose colors to be used in the design.

Requirements
Must have
• The card must be look something that is relevant to the service that I am providing. My website is: www.velmora-buildworks.com
• You can see my website to get more information on what service that I am doing
Nice to have
• On the back of my card, I would like to have a globe image with the incorporation of my company logo. This is to indicate that my services can be done in any part of the world.

```html
<!DOCTYPE html>
<html lang="en">
<head>
<meta charset="utf-8">
<title>Velmora Buildworks – Business Card</title>
<link rel="stylesheet" href="https://fonts.googleapis.com/css2?family=Lato:wght@400;700;900&display=swap">
<style>
  :root {
    --backdrop: #2b2b2b;
    --card: #ffffff;
    --brand-red: #e8202a;
    --ink: #333333;
    --ink-soft: #555555;
    --wordmark-grey: #4a4a4a;
    --divider: #cfcfcf;
    --globe-core: #dedede;
    --globe-mid: #ebebeb;
    --globe-edge: #f6f6f6;
  }
  * { box-sizing: border-box; margin: 0; padding: 0; }
  html, body { width: 1200px; height: 900px; overflow: hidden; }
  body {
    background: var(--backdrop);
    font-family: "Lato", sans-serif;
    position: relative;
  }
  .card {
    position: absolute;
    width: 560px;
    height: 320px;
    background: var(--card);
    border-radius: 18px;
    overflow: hidden;
  }
  .card--front { left: 60px; top: 90px; }
  .card--back { left: 580px; top: 490px; }

  /* shared brand lockup */
  .brand-lockup {
    display: flex;
    align-items: center;
    gap: 12px;
  }
  .brand-dot {
    width: 26px; height: 26px;
    border-radius: 50%;
    background: var(--brand-red);
    flex: none;
  }
  .wordmark {
    font-weight: 900;
    color: var(--wordmark-grey);
    letter-spacing: 2px;
    font-size: 22px;
    line-height: 1.15;
  }

  /* front */
  .card--front .brand-lockup {
    position: absolute;
    left: 36px;
    top: 142px;
  }
  .divider {
    position: absolute;
    left: 300px; top: 56px;
    height: 190px;
    width: 1px;
    background: var(--divider);
  }
  .contact {
    position: absolute;
    left: 320px; top: 58px;
    width: 232px;
  }
  .contact__name {
    color: var(--brand-red);
    font-weight: 900;
    font-size: 18px;
    line-height: 1.1;
  }
  .contact__title {
    color: var(--ink-soft);
    font-size: 13.5px;
    margin-bottom: 12px;
  }
  .contact__list { list-style: none; }
  .contact__item {
    display: flex;
    align-items: flex-start;
    gap: 8px;
    color: var(--ink);
    font-size: 13px;
    line-height: 1.35;
    margin-bottom: 4px;
  }
  .contact__item--address { margin-top: 10px; }
  .contact__icon { width: 13px; height: 13px; flex: none; margin-top: 2px; }

  /* back */
  .globe {
    position: absolute;
    left: 110px; top: 50px;
    width: 380px; height: 240px;
    border-radius: 50%;
    background: radial-gradient(ellipse at 50% 45%, var(--globe-core) 0%, var(--globe-mid) 55%, var(--globe-edge) 100%);
  }
  .card--back .brand-lockup {
    position: absolute;
    left: 150px;
    top: 128px;
    gap: 14px;
  }
  .card--back .wordmark { font-size: 27px; letter-spacing: 3px; }
  .card--back .brand-dot { width: 30px; height: 30px; }
</style>
</head>
<body>

<section class="card card--front" aria-label="Business card front">
  <div class="brand-lockup">
    <span class="brand-dot"></span>
    <p class="wordmark">VELMORA<br>BUILDWORKS</p>
  </div>
  <div class="divider"></div>
  <div class="contact">
    <p class="contact__name">DANIEL REYES</p>
    <p class="contact__title">President</p>
    <ul class="contact__list">
      <li class="contact__item">
        <svg class="contact__icon" viewBox="0 0 16 16"><path fill="#e8202a" d="M3.5 1.5l2.5 0 1 3.5-1.8 1.2a8 8 0 0 0 4.6 4.6l1.2-1.8 3.5 1v2.5c0 .8-.7 1.5-1.5 1.5A12 12 0 0 1 2 3c0-.8.7-1.5 1.5-1.5z"/></svg>
        <span>+974 70428816</span>
      </li>
      <li class="contact__item">
        <svg class="contact__icon" viewBox="0 0 16 16"><rect x="1" y="3" width="14" height="10" rx="1" fill="#e8202a"/><path d="M1.5 3.5L8 9l6.5-5.5" stroke="#fff" stroke-width="1.3" fill="none"/></svg>
        <span>info@velmora-buildworks.com</span>
      </li>
      <li class="contact__item">
        <svg class="contact__icon" viewBox="0 0 16 16"><g fill="none" stroke="#e8202a" stroke-width="1.3"><circle cx="8" cy="8" r="6.5"/><ellipse cx="8" cy="8" rx="3" ry="6.5"/><path d="M1.5 8h13M2.5 4.5h11M2.5 11.5h11"/></g></svg>
        <span>www.velmora-buildworks.com</span>
      </li>
      <li class="contact__item contact__item--address">
        <svg class="contact__icon" viewBox="0 0 16 16"><path fill="#e8202a" d="M8 0.5a5.5 5.5 0 0 0-5.5 5.5C2.5 10 8 15.5 8 15.5S13.5 10 13.5 6A5.5 5.5 0 0 0 8 0.5z"/><circle cx="8" cy="6" r="2" fill="#fff"/></svg>
        <span>P.O. Box 4120,<br>Al Waab Street, Doha - Qatar</span>
      </li>
    </ul>
  </div>
</section>

<section class="card card--back" aria-label="Business card back">
  <div class="globe" role="img" aria-label="Faint grey world map globe behind the company name, showing worldwide service"></div>
  <div class="brand-lockup">
    <span class="brand-dot"></span>
    <p class="wordmark">VELMORA<br>BUILDWORKS</p>
  </div>
</section>

</body>
</html>
```